New web design for a service provider in the medical field

We are looking for a new design for our website. We are a company that repairs and sells medical endoscopes. Our customers include doctors and hospitals. Our current website can be found at https://lumavex.de/en/lumavex-english.
We need a new web design (without programming) for the following 3 pages:
-Startpage https://lumavex.de/en/lumavex-english/
-Used endoscopes https://lumavex.de/en/used-endoscopes/
-Purchase https://lumavex.de/en/purchase/
The design should be modern and stylish.
The blue color of the logo should be reflected on the page, but not too intrusive.
I have uploaded the images from the header. If more images are needed, let me know and I will upload them.

Target Market(s)
Doctors and hospitals

```html
<!DOCTYPE html>
<html lang="en">
<head>
<meta charset="utf-8">
<title>Lumavex – Endoscope Repair</title>
<link href="https://fonts.googleapis.com/css2?family=Josefin+Sans:wght@400;600;700&family=Outfit:wght@500;600;700&display=swap" rel="stylesheet">
<style>
:root{
  --blue:#1fa3e0;
  --blue-dark:#1789c4;
  --navy:#1b3a52;
  --navy-deep:#142d40;
  --ink:#1f2a33;
  --text:#44505a;
  --light:#eef4f8;
  --line:#dde5eb;
  --white:#ffffff;
}
*{box-sizing:border-box;margin:0;padding:0}
html,body{width:1200px;height:4902px;overflow:hidden}
body{font-family:"Josefin Sans",sans-serif;color:var(--text);background:var(--white);position:relative}
.abs{position:absolute}
section,header,footer{position:absolute;left:0;width:1200px;overflow:hidden}
h1,h2,h3,h4{font-family:"Outfit",sans-serif;color:var(--ink);font-weight:700}
.accent{color:var(--blue)}
.btn{position:absolute;display:flex;align-items:center;justify-content:center;font-family:"Outfit",sans-serif;font-weight:600;font-size:12px;letter-spacing:.5px;color:var(--white);text-transform:uppercase}
.btn-blue{background:var(--blue);border-radius:0 22px 22px 22px}
.btn-navy{background:var(--navy);border-radius:22px}
.btn-pill{background:var(--blue);border-radius:22px}

/* header */
.site-header{top:0;height:112px;background:var(--white);z-index:5}
.topbar{position:absolute;right:0;top:0;width:520px;height:38px;background:var(--blue);clip-path:polygon(22px 0,100% 0,100% 100%,0 100%);display:flex;align-items:center;gap:28px;padding-left:40px;color:var(--white);font-size:12px;font-weight:600}
.topbar span{display:flex;align-items:center;gap:8px}
.topbar i{display:inline-block;width:18px;height:18px;border-radius:50%;background:var(--white)}
.logo-disc{position:absolute;left:88px;top:-30px;width:170px;height:155px;border-radius:50%;background:var(--white);box-shadow:0 4px 12px rgba(0,0,0,.06)}
.logo{position:absolute;display:flex;align-items:center;gap:8px;font-family:"Josefin Sans",sans-serif;font-weight:700;color:var(--navy)}
.logo b{display:inline-block;border-radius:50%;background:var(--blue)}
.nav{position:absolute;top:68px;left:305px;display:flex;gap:30px;font-family:"Outfit",sans-serif;font-size:12px;font-weight:600;color:var(--ink)}
.nav a{color:inherit;text-decoration:none;padding-bottom:8px}
.nav a.active{border-bottom:2px solid var(--blue)}

/* hero */
.hero{top:112px;height:560px;background:linear-gradient(100deg,#f4f6f8 0%,#e9edf0 45%,#c9d1d7 100%)}
.hero-photo{position:absolute;left:470px;top:0;width:730px;height:560px;background:linear-gradient(120deg,#dfe4e8,#f7f8f9 40%,#b9c2c9 80%)}
.hero-kicker{position:absolute;left:103px;top:168px;font-size:20px;color:var(--blue);font-weight:400}
.hero h1{position:absolute;left:103px;top:198px;font-size:38px;line-height:46px;color:var(--navy)}

/* service intro */
.intro{top:672px;height:273px;text-align:center}
.section-title{font-size:34px;text-transform:uppercase;letter-spacing:.3px}
.title-bar{width:70px;height:3px;background:var(--blue);margin:10px auto 0}
.intro p{font-size:18px;line-height:32px;width:720px;margin:20px auto 0;color:var(--text)}

/* split */
.split{top:945px;height:507px}
.split-photo-bg{position:absolute;left:0;top:0;width:445px;height:507px;background:linear-gradient(140deg,#39b4ea,#1379b8)}
.split-frame{position:absolute;left:88px;top:52px;width:425px;height:372px;border:3px solid var(--white)}
.split-photo{position:absolute;left:104px;top:73px;width:408px;height:339px;background:linear-gradient(135deg,#f6f6f6,#d9dcde)}
.split-copy{position:absolute;left:602px;top:68px;width:470px}
.split-copy h3{font-family:"Josefin Sans",sans-serif;font-weight:600;font-size:25px;line-height:35px;color:var(--ink)}
.split-copy p{font-size:13.5px;line-height:23px;margin-top:18px;color:var(--text)}
.split-copy p+p{margin-top:12px}

/* repair & sale */
.offers{top:1452px;height:1133px;background:linear-gradient(180deg,var(--white),var(--light))}
.offers-top{position:absolute;left:0;top:0;width:1200px;height:423px;background:linear-gradient(160deg,#234661,var(--navy) 60%,var(--navy-deep))}
.offers-title{position:absolute;top:68px;left:0;width:1200px;text-align:center;color:var(--white);font-size:32px}
.offers-lead{position:absolute;top:124px;left:0;width:1200px;text-align:center;color:var(--white);font-size:15.5px;line-height:24px}
.diamond{position:absolute;width:262px;height:262px;transform:rotate(45deg);background:var(--blue)}
.diamond.dark{background:#2b4860;border:3px solid var(--white);outline:2px solid var(--navy);box-shadow:0 0 0 6px rgba(43,72,96,.6)}
.diamond-text{position:absolute;width:240px;text-align:center;color:var(--white)}
.diamond-text h4{color:var(--white);font-size:18px;letter-spacing:.3px}
.diamond-text .sub{font-size:14px;margin-top:4px}
.diamond-text .tiny{font-size:9px;line-height:13px;margin-top:8px;opacity:.9}
.faulty-photo{position:absolute;left:590px;top:630px;width:518px;height:380px;background:linear-gradient(180deg,#f3f5f7,#e2e6ea)}
.faulty-border{position:absolute;left:115px;top:668px;width:542px;height:390px;border-top:8px solid var(--blue);border-left:8px solid var(--blue)}
.faulty-card{position:absolute;left:123px;top:676px;width:534px;height:379px;background:var(--white);box-shadow:0 8px 30px rgba(27,58,82,.08);padding:58px 56px}
.faulty-title{font-size:30px;line-height:36px;color:var(--ink)}
.faulty-sub{font-family:"Josefin Sans",sans-serif;font-weight:400;font-size:22px;margin-top:20px;color:var(--ink)}
.faulty-card p{font-size:15px;line-height:25px;margin-top:10px}

/* outcome */
.outcome{top:2585px;height:705px}
.outcome .section-title{position:absolute;top:70px;width:1200px;text-align:center;font-size:30px}
.grid{position:absolute;left:133px;top:165px;width:932px;height:445px}
.cell{position:absolute;width:310px;padding:0 40px}
.cell svg{display:block;margin-bottom:14px}
.cell h4{font-size:17px;line-height:20px;color:var(--ink)}
.cell p{font-size:13.5px;line-height:19px;margin-top:10px}
.cell.feature{background:linear-gradient(135deg,#2fb1ea,#1592d4);color:var(--white)}
.cell.feature h4,.cell.feature p{color:var(--white)}
.vline{position:absolute;width:1px;background:var(--line)}
.hline{position:absolute;height:1px;background:var(--line)}

/* decision */
.decision{top:3290px;height:730px;background:var(--navy)}
.decision-title{position:absolute;top:108px;left:0;width:1200px;text-align:center;color:var(--white);font-size:27px;line-height:32px}
.feat{position:absolute;width:300px;color:var(--white)}
.feat h4{color:var(--white);font-size:14px}
.feat p{font-size:10px;line-height:15px;margin-top:4px;color:#c6d3dd}
.feat.left{text-align:right}

/* help */
.help{top:4020px;height:500px;background:linear-gradient(180deg,var(--light),#f7fafc)}
.help .section-title{position:absolute;top:60px;width:1200px;text-align:center;font-size:30px}
.help-lead{position:absolute;top:112px;left:0;width:1200px;text-align:center;font-size:14.5px;line-height:21px}
.field{position:absolute;background:var(--white);border:1px solid #cfd9e0;display:flex;align-items:center;gap:10px;padding-left:16px;font-family:"Outfit",sans-serif;font-size:12.5px;font-weight:500;color:var(--ink)}
.field.area{align-items:flex-start;padding-top:16px}

/* footer */
.site-footer{top:4520px;height:382px;background:var(--white)}
.foot-col{position:absolute;top:88px;border-left:3px solid var(--blue);padding-left:18px}
.foot-col h5{font-family:"Outfit",sans-serif;font-size:13.5px;font-weight:600;color:var(--ink)}
.foot-col a{display:block;font-size:13px;color:var(--text);text-decoration:none;margin-top:12px}
.socials{display:flex;gap:6px;margin-top:18px}
.socials b{width:28px;height:28px;border-radius:50%;background:var(--navy)}
.copyright{position:absolute;top:350px;width:1200px;text-align:center;font-size:11.5px;color:var(--text)}
</style>
</head>
<body>

<header class="site-header">
  <div class="topbar">
    <span><i></i>info@lumavex.de</span>
    <span><i></i>+49 4000 555 210-0</span>
    <span>ENG ⌄</span>
  </div>
  <div class="logo-disc"></div>
  <div class="logo" style="left:108px;top:42px;font-size:24px"><b style="width:14px;height:14px"></b>Lumavex</div>
  <nav class="nav">
    <a class="active" href="#">ENDOSCOPE REPAIR</a>
    <a href="#">ENDOSCOPY SYSTEMS</a>
    <a href="#">ENDOSCOPY ACCESSORIES ⌄</a>
    <a href="#">ACCESSORIES CATALOG</a>
    <a href="#">PURCHASE</a>
  </nav>
</header>

<section class="hero">
  <div class="hero-photo" role="img" aria-label="Close-up photo of a white flexible endoscope control body with black angulation knobs"></div>
  <svg class="abs" style="left:0;top:0" width="1200" height="560" viewBox="0 0 1200 560">
    <polygon points="0,560 0,555 760,520 1200,495 1200,560" fill="#ffffff"/>
    <polygon points="420,560 1200,492 1200,560" fill="var(--blue)"/>
  </svg>
  <div class="hero-kicker">WELCOME TO LUMAVEX</div>
  <h1>PUT YOUR ENDOSCOPE<br>IN RELIABLE HANDS!</h1>
  <div class="btn btn-blue" style="left:103px;top:310px;width:165px;height:44px">Learn more</div>
</section>

<section class="intro">
  <h2 class="section-title" style="margin-top:40px">Your future <span class="accent">our service</span></h2>
  <div class="title-bar"></div>
  <p>Lumavex GmbH is specialised in the repair and sale of Orvana, Pentrel and Fujora flexible medical endoscopes. As a service-oriented company, we are at your side with our knowledge and skills!</p>
</section>

<section class="split">
  <div class="split-photo-bg" role="img" aria-label="Blue-toned photo of a medical workshop"></div>
  <div class="split-frame"></div>
  <div class="split-photo" role="img" aria-label="Photo of two black endoscope handles on a white surface"></div>
  <div class="split-copy">
    <h3>Endoscope repairs and second hand endoscopes from Lumavex cause the outcome matters!</h3>
    <p>Lumavex is a privileged partner for the start-up facility or optimisation of existing healthcare facilities, doctor's offices and hospitals. The quality and reliability of our products and our offered service are our best advertisement!</p>
    <p>As a result of optimised processes and highly qualified specialists in our company, we can work very quickly and with high quality for your benefit of least possible restrictions in your doctor's office or in your hospital.</p>
  </div>
</section>

<section class="offers">
  <div class="offers-top" role="img" aria-label="Dark blue photo of endoscope cables"></div>
  <h2 class="offers-title">REPAIR &amp; SALE ENDOSCOPE</h2>
  <p class="offers-lead">Lorem ipsum dolor sit amet, consectetur adipiscing elit, sed do eiusmod tempor incidi-<br>dunt ut labore et dolore magna aliqua. Ut enim ad minim veniam</p>

  <div class="diamond" style="left:160px;top:292px"></div>
  <div class="diamond dark" style="left:494px;top:292px"></div>
  <div class="diamond" style="left:825px;top:292px"></div>

  <div class="diamond-text" style="left:171px;top:312px">
    <svg width="64" height="46" viewBox="0 0 64 46" fill="none" stroke="#fff" stroke-width="2"><circle cx="20" cy="23" r="13"/><circle cx="20" cy="23" r="7"/><path d="M33 18h24M33 28h24M57 18v10"/></svg>
    <h4>REPAIR</h4>
    <div class="sub">Endoscope repair service</div>
    <div class="tiny">Independent of the maker, we repair and maintain endoscopes and their individual parts.</div>
  </div>
  <div class="diamond-text" style="left:505px;top:290px">
    <svg width="50" height="50" viewBox="0 0 50 50" fill="none" stroke="#fff" stroke-width="2"><path d="M18 8h14v14l-7 6-7-6z"/><path d="M25 28v12c0 4 6 4 6 0"/></svg>
    <h4>SALE</h4>
    <div class="sub">Used endoscopes</div>
    <div class="tiny">Our regular stock includes refurbished gastroscopes, colonoscopes, bronchoscopes and cystoscopes from well-known makers Orvana, Pentrel and Fujora.</div>
    <div class="btn btn-pill" style="position:relative;margin:10px auto 0;width:120px;height:28px;font-size:10px">Learn more</div>
  </div>
  <div class="diamond-text" style="left:836px;top:300px">
    <svg width="50" height="54" viewBox="0 0 50 54" fill="none" stroke="#fff" stroke-width="2"><rect x="16" y="6" width="18" height="22" rx="3"/><path d="M25 28v16M18 36h14"/></svg>
    <h4>PURCHASE</h4>
    <div class="sub">Used endoscopes</div>
    <div class="tiny">We buy used endoscopes, even faulty and dismantled ones. Contact us now for a fair purchase offer!</div>
  </div>

  <div class="faulty-photo" role="img" aria-label="Photo of several black flexible endoscopes hanging in a row"></div>
  <div class="faulty-border"></div>
  <div class="faulty-card">
    <h2 class="faulty-title">FAULTY <span class="accent">ENDOSCOPE?</span></h2>
    <h3 class="faulty-sub">We ensure quick and smooth repairs!</h3>
    <p>Lorem ipsum dolor sit amet, consectetur adipiscing elit, sed do eiusmod tempor incididunt ut labore et dolore magna aliqua. Ut enim ad minim veniam, quis nostrud exercitation ullamco laboris n</p>
    <div class="btn btn-navy" style="left:56px;top:300px;width:164px;height:44px">Pick up order</div>
  </div>
</section>

<section class="outcome">
  <h2 class="section-title">Cause the <span class="accent">outcome matters</span></h2>
  <div class="grid">
    <div class="vline" style="left:300px;top:0;height:445px"></div>
    <div class="vline" style="left:640px;top:0;height:445px"></div>
    <div class="hline" style="left:0;top:235px;width:932px"></div>

    <div class="cell feature" style="left:0;top:0;width:300px;height:235px;padding-top:48px">
      <svg width="44" height="44" viewBox="0 0 44 44" fill="none" stroke="#fff" stroke-width="2"><circle cx="22" cy="22" r="14"/><circle cx="22" cy="22" r="5"/></svg>
      <h4>One company for<br>everyone</h4>
      <p>We are a service provider for doctors and hospitals!</p>
    </div>
    <div class="cell" style="left:300px;top:40px;width:340px">
      <svg width="56" height="56" viewBox="0 0 56 56" fill="none" stroke="var(--navy)" stroke-width="2"><circle cx="28" cy="16" r="8"/><path d="M12 46c0-10 8-16 16-16s16 6 16 16z" fill="#9fd7f3"/></svg>
      <h4>Experience<br>characterises us</h4>
      <p>Our team has many years of experience in the business field!</p>
    </div>
    <div class="cell" style="left:640px;top:30px;width:292px">
      <svg width="50" height="66" viewBox="0 0 50 66" fill="none" stroke="var(--navy)" stroke-width="2"><rect x="14" y="6" width="18" height="24" rx="3" fill="#9fd7f3"/><path d="M23 30v22c0 6 10 6 10 0"/></svg>
      <h4>The product is close<br>to our hearts</h4>
      <p>We repair and sell second hand, flexible endoscopes!</p>
    </div>
    <div class="cell" style="left:0;top:270px;width:300px">
      <svg width="48" height="52" viewBox="0 0 48 52" fill="none" stroke="var(--navy)" stroke-width="2"><path d="M24 4l18 7v14c0 12-8 20-18 24C14 45 6 37 6 25V11z"/><circle cx="24" cy="26" r="9" fill="#9fd7f3"/><path d="M19 26l4 4 7-7"/></svg>
      <h4>Guaranteed service</h4>
      <p>You receive a six-month warranty on all repairs!</p>
    </div>
    <div class="cell" style="left:300px;top:270px;width:340px">
      <svg width="60" height="52" viewBox="0 0 60 52" fill="none" stroke="var(--navy)" stroke-width="2"><path d="M30 4l4 8 9 1-7 6 2 9-8-5-8 5 2-9-7-6 9-1z"/><path d="M4 40h14l10 6h24" stroke="var(--blue)"/></svg>
      <h4>Quality not quantity</h4>
      <p>Reliability and durability instead of inferior replacements!</p>
    </div>
    <div class="cell" style="left:640px;top:270px;width:292px">
      <svg width="52" height="56" viewBox="0 0 52 56" fill="none" stroke="var(--navy)" stroke-width="2"><path d="M22 4l16 6v14c0 12-7 20-16 24C13 44 6 36 6 24V10z"/><circle cx="34" cy="38" r="9" fill="#9fd7f3"/><circle cx="34" cy="38" r="3"/></svg>
      <h4>Services for everyone</h4>
      <p>Our service includes the manufacturers Orvana, Pentrel and Fujora!</p>
    </div>
  </div>
</section>

<section class="decision">
  <svg class="abs" style="left:0;top:0" width="1200" height="730" viewBox="0 0 1200 730">
    <polygon points="0,0 1200,0 1200,10 0,58" fill="#ffffff"/>
    <polygon points="0,30 300,18 0,58" fill="var(--blue)"/>
    <polygon points="0,730 0,700 1200,680 1200,730" fill="var(--light)"/>
    <polygon points="700,700 1200,640 1200,685" fill="var(--blue)"/>
    <circle cx="600" cy="380" r="156" fill="none" stroke="#2f5674" stroke-width="2"/>
    <path d="M480 280 A156 156 0 0 1 720 280" fill="none" stroke="var(--blue)" stroke-width="3"/>
    <circle cx="600" cy="380" r="122" fill="#f1f5f8"/>
    <g fill="none" stroke="#fff" stroke-width="2">
      <circle cx="452" cy="262" r="27" stroke="#3a6585"/><path d="M442 252l20 20M462 252l-20 20"/>
      <circle cx="412" cy="375" r="27" stroke="#3a6585"/><circle cx="412" cy="375" r="9"/>
      <circle cx="440" cy="490" r="27" stroke="#3a6585"/><rect x="428" y="480" width="24" height="18"/>
      <circle cx="740" cy="262" r="27" stroke="#3a6585"/><circle cx="740" cy="262" r="9"/>
      <circle cx="786" cy="375" r="27" stroke="#3a6585"/><path d="M774 380h24l-4-12h-16z"/>
      <circle cx="740" cy="490" r="27" stroke="#3a6585"/><path d="M740 480l3 6 7 1-5 5 1 7-6-3-6 3 1-7-5-5 7-1z"/>
    </g>
  </svg>
  <div class="logo" style="left:540px;top:366px;font-size:24px"><b style="width:12px;height:12px"></b>Lumavex</div>
  <h2 class="decision-title">LUMAVEX GMBH, YOUR DECISION<br>FOR YOUR FUTURE</h2>

  <div class="feat left" style="left:104px;top:232px"><h4>Fast Repairs</h4><p>Keep potential disruptions in your doctor's<br>office or in your hospital at minimum</p></div>
  <div class="feat left" style="left:56px;top:348px"><h4>On-site service</h4><p>We will gladly pay you a visit to carry<br>out analysis and repairs on site. Due to our<br>many years of experience</p></div>
  <div class="feat left" style="left:94px;top:478px"><h4>Without a maintenance contract</h4><p>No subscription or other maintenance contract,<br>but one-time and sustainable repair work</p></div>
  <div class="feat" style="left:786px;top:232px"><h4>Highly cost efficient</h4><p>Benefit from our first class recommendations<br>and implementation by our experienced staff.</p></div>
  <div class="feat" style="left:826px;top:348px"><h4>Loan equipment service</h4><p>We will gladly pay you a visit to to carry<br>out analysis and repairs on site. Due to our<br>many years of experience</p></div>
  <div class="feat" style="left:786px;top:478px"><h4>First class service</h4><p>Our clients always come first!</p></div>

  <div class="btn btn-pill" style="left:477px;top:588px;width:275px;height:44px;text-transform:none;font-size:13px">Learn more about Lumavex</div>
</section>

<section class="help">
  <h2 class="section-title">How can we help you?</h2>
  <p class="help-lead">Lorem ipsum dolor sit amet, consectetur adipiscing elit, sed do eiusmod tempor incididunt<br>ut labore et dolore magna aliqua. Ut enim ad minim veniam, quis nostrud</p>
  <div class="field" style="left:210px;top:192px;width:396px;height:50px"><svg width="12" height="12" viewBox="0 0 12 12" fill="#9aa7b1"><circle cx="6" cy="3.5" r="3"/><path d="M0 12c0-4 3-5 6-5s6 1 6 5z"/></svg>First name</div>
  <div class="field" style="left:210px;top:246px;width:396px;height:50px"><svg width="12" height="12" viewBox="0 0 12 12" fill="#9aa7b1"><path d="M2 0h3l1 3-2 1c1 2 2 3 4 4l1-2 3 1v3c0 1-1 2-2 2C5 12 0 7 0 2c0-1 1-2 2-2z"/></svg>Phone number</div>
  <div class="field" style="left:210px;top:300px;width:396px;height:50px"><svg width="14" height="10" viewBox="0 0 14 10" fill="none" stroke="#9aa7b1" stroke-width="1.4"><rect x="1" y="1" width="12" height="8"/><path d="M1 1l6 5 6-5"/></svg>Email address</div>
  <div class="field area" style="left:616px;top:192px;width:396px;height:158px">Comments</div>
  <div class="btn btn-navy" style="left:522px;top:385px;width:160px;height:42px">Submit now</div>
</section>

<footer class="site-footer">
  <div class="logo" style="left:125px;top:100px;font-size:24px"><b style="width:12px;height:12px"></b>Lumavex</div>
  <p class="abs" style="left:125px;top:182px;width:270px;font-size:12px;line-height:16px">Lorem ipsum dolor sit amet, consectetur adipiscing elit, sed do eiusmod tempor incididunt ut labore et dolore</p>
  <div class="foot-col" style="left:467px;height:150px">
    <h5>NAVIGATION</h5>
    <a href="#">Home</a><a href="#">Endoscope Repair</a><a href="#">Used Endoscope</a><a href="#">Endoscopy Systems</a>
  </div>
  <div class="foot-col" style="left:707px;height:150px">
    <h5>RESOURCES</h5>
    <a href="#">Endoscopy Accesories</a><a href="#">Purchase</a><a href="#">Contact Us</a>
  </div>
  <div class="foot-col" style="left:915px;border-left-color:transparent">
    <h5>FOLLOW US</h5>
    <div class="socials"><b></b><b></b><b></b><b></b></div>
  </div>
  <div class="hline" style="left:0;top:328px;width:1200px"></div>
  <div class="copyright">© 2022 Lumavex GmbH</div>
</footer>

</body>
</html>
```